Calvanto Group Real Estate Company business cards

New business card design, we are generally happy with the basic layout of the existing front of business card, (feel free to change) but require a head shot photo on the back side.

http://www.calvanto.com.au/

Attached logos, and existing business card

------------------------------

Target Market(s)

Real estate

Industry/Entity Type

Real Estate

Contact Information for Business Card

Standard size double sided

Font styles to use
Other font styles liked:
• Futura

Requirements
Must have
• Photo head shot on the back side
Nice to have
• yes
Should not have
• No

```html
<!DOCTYPE html>
<html lang="en">
<head>
<meta charset="utf-8">
<title>Calvanto Group – Business Cards</title>
<link rel="stylesheet" href="https://fonts.googleapis.com/css2?family=Jost:wght@400;500;600&display=swap">
<style>
  :root{
    --bg:#e9e6e1;
    --purple:#3a2a78;
    --purple-deep:#2c1f61;
    --orange:#f7931e;
    --white:#ffffff;
    --grey:#6b6b6b;
  }
  *{box-sizing:border-box;margin:0;padding:0}
  html,body{width:1200px;height:950px;overflow:hidden}
  body{background:var(--bg);font-family:"Jost",Futura,"Century Gothic",sans-serif;position:relative}

  .card{position:absolute;background:var(--white);box-shadow:0 10px 28px rgba(0,0,0,.22);overflow:hidden}

  /* Front */
  .card-front{left:100px;top:315px;width:560px;height:320px}
  .front-brand{position:absolute;left:0;top:0;width:300px;height:320px;display:flex;flex-direction:column;align-items:center;justify-content:center;gap:12px}
  .front-panel{position:absolute;left:0;top:0;width:560px;height:320px}
  .contact{position:absolute;right:26px;top:30px;text-align:right;color:var(--white);font-size:15px;line-height:1.6;letter-spacing:.2px}
  .contact-row{display:flex;justify-content:flex-end;align-items:center;gap:8px}
  .contact-row svg{width:14px;height:14px}
  .person{position:absolute;left:332px;top:206px;color:var(--white)}
  .person-name{color:var(--orange);font-weight:600;font-size:22px;line-height:1.2}
  .person-role{font-size:15px;margin-top:4px}
  .person-email{font-size:14px;margin-top:4px;letter-spacing:.2px}

  /* Brand */
  .brand{display:flex;align-items:center;gap:10px;color:var(--purple);font-weight:500;font-size:38px;letter-spacing:.5px;line-height:1}
  .brand-dot{width:12px;height:12px;border-radius:50%;background:var(--orange)}
  .tagline{color:var(--purple);font-weight:600;font-size:15px;letter-spacing:1px;word-spacing:4px}

  /* Back */
  .card-back{left:760px;top:195px;width:320px;height:560px}
  .headshot{position:absolute;left:0;top:0;width:320px;height:400px;background:linear-gradient(180deg,#f79a28 0%,#f39015 100%)}
  .headshot-figure{position:absolute;left:40px;top:90px;width:240px;height:310px;border-radius:110px 110px 0 0;background:linear-gradient(180deg,#2f3650 0%,#262c44 100%);opacity:.85}
  .back-brand{position:absolute;left:0;top:400px;width:320px;height:160px;display:flex;flex-direction:column;align-items:center;justify-content:center;gap:8px}
  .back-brand .brand{font-size:30px}
  .back-brand .tagline{font-size:13px}
  .website{color:var(--grey);font-size:14px;letter-spacing:3px}
</style>
</head>
<body>

<section class="card card-front" aria-label="Business card front">
  <svg class="front-panel" viewBox="0 0 560 320" aria-hidden="true">
    <path d="M304 0 H560 V320 H304 V232 L288 220 L304 208 Z" fill="var(--purple)"/>
    <path d="M300 0 V204 L280 220 L300 236 V320" fill="none" stroke="var(--orange)" stroke-width="4"/>
  </svg>

  <div class="front-brand">
    <div class="brand"><span class="brand-dot"></span>Calvanto Group</div>
    <div class="tagline">Buy | Sell | Rent</div>
  </div>

  <div class="contact">
    <div>Calvanto Group</div>
    <div class="contact-row">0412 555 308
      <svg viewBox="0 0 24 24"><path fill="var(--orange)" d="M6.6 10.8a15 15 0 0 0 6.6 6.6l2.2-2.2a1 1 0 0 1 1-.25 11.4 11.4 0 0 0 3.6.57 1 1 0 0 1 1 1V20a1 1 0 0 1-1 1A17 17 0 0 1 3 4a1 1 0 0 1 1-1h3.5a1 1 0 0 1 1 1c0 1.25.2 2.45.57 3.57a1 1 0 0 1-.25 1z"/></svg>
    </div>
    <div class="contact-row">calvanto.com.au
      <svg viewBox="0 0 24 24"><circle cx="12" cy="12" r="10" fill="var(--orange)"/><path d="M2 12h20M12 2c3 3 3 17 0 20M12 2c-3 3-3 17 0 20" stroke="var(--purple)" stroke-width="1.5" fill="none"/></svg>
    </div>
    <div>ABN: 41 902 386 157</div>
  </div>

  <div class="person">
    <div class="person-name">Daniel Tran</div>
    <div class="person-role">Director</div>
    <div class="person-email">daniel.tran@calvanto.com.au</div>
  </div>
</section>

<section class="card card-back" aria-label="Business card back">
  <div class="headshot" role="img" aria-label="Head shot photo of the director in a navy suit and blue tie">
    <div class="headshot-figure"></div>
  </div>
  <div class="back-brand">
    <div class="brand"><span class="brand-dot"></span>Calvanto Group</div>
    <div class="tagline">Buy | Sell | Rent</div>
    <div class="website">www.calvanto.com.au</div>
  </div>
</section>

</body>
</html>
```